Opening a Hair Salon

Looking for a design for my sign that looks high end, an emphasis on color but welcoming to men and women.

The name is Corvane Haircuts and Colors

Trying capture a more affluent client. Looking for a very modern look.

Reason: Time is going to quick and would like to see a few more options.

```html
<!DOCTYPE html>
<html lang="en">
<head>
<meta charset="utf-8">
<title>Corvane Haircuts and Colors – Banner Options</title>
<link href="https://fonts.googleapis.com/css2?family=Mulish:wght@400;800&family=Oswald:wght@500;600&display=swap" rel="stylesheet">
<style>
  :root{
    --stage-dark:#1b1b1b;
    --stage-light:#5a5a5a;
    --frame:#f3e6b5;
    --glow:rgba(255,240,190,.55);
    --ink:#111111;
    --plum:#5a0f45;
    --magenta:#e0129c;
    --cyan:#2ab4d1;
    --sky-1:#d9f6fb;
    --sky-2:#a9e6f4;
    --sand-1:#efe6d2;
    --sand-2:#d9c89b;
    --panel:#121212;
    --white:#ffffff;
  }
  *{margin:0;padding:0;box-sizing:border-box}
  html,body{width:1200px;height:1000px;overflow:hidden}
  body{
    position:relative;
    background:radial-gradient(ellipse at 50% 20%, var(--stage-light) 0%, #333 45%, var(--stage-dark) 100%);
    font-family:"Mulish",sans-serif;
  }
  .banner{
    position:absolute;left:60px;width:1087px;height:273px;
    border:2px solid var(--frame);
    box-shadow:0 0 14px 3px var(--glow);
    overflow:hidden;
  }
  .banner > *{z-index:2}
  .banner > .photo{z-index:1}
  .banner--one{top:61px}
  .banner--two{top:377px}
  .banner--three{top:687px}
  .banner--sky{background:linear-gradient(100deg,var(--sky-1) 0%,var(--sky-2) 55%,var(--sky-1) 100%)}
  .banner--sand{background:linear-gradient(100deg,var(--sand-1) 0%,var(--sand-2) 50%,#f4efe6 100%)}

  .amenities{position:absolute;left:0;top:0;width:410px;height:102px}
  .amenity{
    position:absolute;display:flex;align-items:center;gap:10px;
    color:var(--white);font-size:9px;font-family:"Mulish",sans-serif;
  }
  .amenity svg{width:14px;height:14px;flex:none}

  .cta{
    position:absolute;font-family:"Oswald",sans-serif;font-weight:500;
    font-size:37px;letter-spacing:-.5px;color:var(--ink);white-space:nowrap;line-height:1;
    transform:scaleX(.93);transform-origin:left;
  }
  .phone{
    position:absolute;font-family:"Oswald",sans-serif;font-weight:600;
    font-size:84px;line-height:1;white-space:nowrap;letter-spacing:-1px;
    -webkit-text-stroke:4px var(--ink);paint-order:stroke fill;
    transform:scaleX(.92);transform-origin:left;
  }
  .phone--magenta{color:var(--magenta)}
  .phone--cyan{color:var(--cyan)}

  .tagline{
    position:absolute;font-family:"Mulish",sans-serif;font-weight:800;
    font-size:31px;line-height:40px;text-align:center;text-transform:uppercase;white-space:nowrap;
  }
  .tagline--ink{color:var(--ink)}
  .tagline--plum{color:var(--plum)}

  .brand{
    position:absolute;display:flex;align-items:center;gap:12px;
    font-family:"Mulish",sans-serif;font-weight:800;color:var(--plum);line-height:1;
  }
  .brand__dot{border-radius:50%;background:var(--magenta);flex:none}

  .photo{position:absolute;top:0;bottom:0}
  .photo--brunette{right:0;width:236px;background:linear-gradient(160deg,#f3d9cf 0%,#6b4a38 45%,#2f211a 100%)}
  .photo--redhead{right:0;width:142px;background:linear-gradient(170deg,#b8331d 0%,#e8c3ab 45%,#8e2412 100%)}
  .photo--reclining{right:0;width:300px;background:linear-gradient(110deg,rgba(169,230,244,0) 0%,rgba(58,42,34,.85) 30%,#f0d2c2 62%,#e9f7fb 100%)}

  .now-open{
    position:absolute;left:0;bottom:0;width:215px;height:44px;
  }
  .now-open span{
    position:absolute;left:44px;top:6px;font-family:"Oswald",sans-serif;font-weight:500;
    font-size:29px;color:var(--white);line-height:1;
  }
</style>
</head>
<body>

<section class="banner banner--one banner--sky">
  <svg class="amenities" viewBox="0 0 410 102" aria-hidden="true">
    <polygon points="0,0 402,0 348,96 0,96" fill="var(--panel)"/>
    <polygon points="402,0 410,0 352,102 0,102 0,96 348,96" fill="var(--magenta)"/>
  </svg>
  <div class="amenity" style="left:34px;top:28px">
    <svg viewBox="0 0 14 14"><path d="M1 5a9 9 0 0 1 12 0M3 7.5a6 6 0 0 1 8 0M5 10a3 3 0 0 1 4 0" stroke="#fff" stroke-width="1.3" fill="none"/><circle cx="7" cy="12" r="1" fill="#fff"/></svg>Free Wifi</div>
  <div class="amenity" style="left:186px;top:28px">
    <svg viewBox="0 0 14 14"><rect x="1" y="4" width="12" height="9" rx="1" stroke="#fff" stroke-width="1.3" fill="none"/><path d="M4 1l3 3 3-3" stroke="#fff" fill="none"/></svg>Cable TV/Movies</div>
  <div class="amenity" style="left:34px;top:61px">
    <svg viewBox="0 0 14 14"><path d="M1 6V1h5l7 7-5 5z" fill="#fff"/><circle cx="4" cy="4" r="1.1" fill="#121212"/></svg>Specials and Promotions</div>
  <div class="amenity" style="left:186px;top:60px">
    <svg viewBox="0 0 14 14"><rect x="1" y="2" width="12" height="11" stroke="#fff" stroke-width="1.3" fill="none"/><text x="7" y="11" font-size="6" fill="#fff" text-anchor="middle" font-family="sans-serif">28</text></svg>Appointments or Walk-Ins</div>

  <div class="cta" style="left:36px;top:131px">MAKE AN APPOINTMENT TODAY!</div>
  <div class="phone phone--magenta" style="left:36px;top:164px">318-5062-947</div>

  <div class="photo photo--brunette" role="img" aria-label="Photo of a woman in profile with long, straight brunette hair"></div>

  <div class="tagline tagline--ink" style="left:475px;top:20px;width:360px">We offer the<br>best style in town</div>
  <div class="brand" style="left:505px;top:168px;font-size:58px">
    <span class="brand__dot" style="width:30px;height:30px"></span>Corvane</div>
</section>

<section class="banner banner--two banner--sand">
  <div class="brand" style="left:40px;top:104px;font-size:76px">
    <span class="brand__dot" style="width:38px;height:38px"></span>Corvane</div>

  <svg class="now-open" viewBox="0 0 215 44" aria-hidden="true">
    <polygon points="0,0 215,0 190,44 0,44" fill="var(--panel)"/>
  </svg>
  <div class="now-open"><span>NOW OPEN</span></div>

  <div class="tagline tagline--plum" style="left:495px;top:18px;width:370px">We offer the<br>best style in town</div>
  <div class="cta" style="left:500px;top:128px">MAKE AN APPOINTMENT TODAY!</div>
  <div class="phone phone--cyan" style="left:500px;top:162px">318-5062-947</div>

  <div class="photo photo--redhead" role="img" aria-label="Photo of a woman with shoulder-length red hair looking at the viewer"></div>
</section>

<section class="banner banner--three banner--sky">
  <svg class="amenities" viewBox="0 0 410 102" aria-hidden="true">
    <polygon points="0,0 402,0 348,96 0,96" fill="var(--panel)"/>
    <polygon points="402,0 410,0 352,102 0,102 0,96 348,96" fill="var(--magenta)"/>
  </svg>
  <div class="amenity" style="left:34px;top:27px">
    <svg viewBox="0 0 14 14"><path d="M1 5a9 9 0 0 1 12 0M3 7.5a6 6 0 0 1 8 0M5 10a3 3 0 0 1 4 0" stroke="#fff" stroke-width="1.3" fill="none"/><circle cx="7" cy="12" r="1" fill="#fff"/></svg>Free Wifi</div>
  <div class="amenity" style="left:186px;top:27px">
    <svg viewBox="0 0 14 14"><rect x="1" y="4" width="12" height="9" rx="1" stroke="#fff" stroke-width="1.3" fill="none"/><path d="M4 1l3 3 3-3" stroke="#fff" fill="none"/></svg>Cable TV/Movies</div>
  <div class="amenity" style="left:34px;top:61px">
    <svg viewBox="0 0 14 14"><path d="M1 6V1h5l7 7-5 5z" fill="#fff"/><circle cx="4" cy="4" r="1.1" fill="#121212"/></svg>Specials and Promotions</div>
  <div class="amenity" style="left:186px;top:60px">
    <svg viewBox="0 0 14 14"><rect x="1" y="2" width="12" height="11" stroke="#fff" stroke-width="1.3" fill="none"/><text x="7" y="11" font-size="6" fill="#fff" text-anchor="middle" font-family="sans-serif">28</text></svg>Appointments or Walk-Ins</div>

  <div class="cta" style="left:36px;top:129px">MAKE AN APPOINTMENT TODAY!</div>
  <div class="phone phone--magenta" style="left:36px;top:163px">318-5062-947</div>

  <div class="photo photo--reclining" role="img" aria-label="Photo of a woman resting her head on her hand, long dark hair spread across a table"></div>

  <div class="tagline tagline--ink" style="left:475px;top:20px;width:360px">We offer the<br>best style in town</div>
  <div class="brand" style="left:505px;top:170px;font-size:58px">
    <span class="brand__dot" style="width:30px;height:30px"></span>Corvane</div>
</section>

</body>
</html>
```